Bulldog themed background for Real Estate Purchase Letter

I need a phantom background or watermark on a standard 8 1/2" x 11" paper. I am going to put a letter over the background. I want a bulldog theme that is cute, funny and original. This letter is for a real estate project and we want to capture the person sub-consciously . Attached is my personal dogs. If you want to use them you can but not required. I have attached the letter that I am trying to emulate. I want bulldogs not horses.

Target Market(s)

45 years old and higher

Industry/Entity Type

Real Estate

Font styles to use
Serif
Sans Serif

Colors

Designer to choose colors to be used in the design.

Requirements
Must have
• fun, happiness, reassuring,
Should not have
• violence, negativity, unhappy

```html
<!DOCTYPE html>
<html lang="en">
<head>
<meta charset="UTF-8">
<title>Property Purchase Letter</title>
<link href="https://fonts.googleapis.com/css2?family=Open+Sans:wght@300;400;600&display=swap" rel="stylesheet">
<style>
  :root {
    --ink: #333a40;
    --ink-strong: #2a3036;
    --blue-deep: #1565d8;
    --blue-mid: #1e8ff0;
    --cyan: #22c4f5;
    --badge: #2167c4;
    --mascot: #d7dee6;
    --paper: #ffffff;
  }
  * { box-sizing: border-box; margin: 0; padding: 0; }
  html, body { width: 850px; height: 1200px; overflow: hidden; background: var(--paper); }
  .letterhead {
    position: relative; width: 850px; height: 1200px; overflow: hidden;
    background: var(--paper);
    font-family: "Open Sans", Arial, sans-serif; font-weight: 300; color: var(--ink);
  }
  .mascot-watermark {
    position: absolute; left: 70px; top: 120px; width: 780px; height: 1080px;
    border-radius: 46% 50% 40% 44%;
    background: radial-gradient(ellipse at 50% 45%, rgba(215,222,230,0.85) 0%, rgba(215,222,230,0.55) 45%, rgba(215,222,230,0) 72%);
  }
  .swoosh { position: absolute; left: 0; top: 0; width: 850px; height: 1200px; }
  .agent-badge {
    position: absolute; left: 458px; top: 44px; width: 360px; height: 35px;
    background: var(--badge); color: #fff;
    font-weight: 600; font-size: 17px; line-height: 35px; padding-left: 14px;
    letter-spacing: 0.2px;
  }
  .recipient { position: absolute; left: 69px; top: 114px; font-size: 17.5px; line-height: 30px; }
  .recipient .name, .signature .name, .salutation strong, .field { font-weight: 600; color: var(--ink-strong); }
  .salutation { position: absolute; left: 69px; top: 248px; font-size: 17.5px; }
  .body-copy { position: absolute; left: 69px; top: 318px; width: 711px; font-size: 17.5px; line-height: 36.5px; }
  .body-copy p { text-align: justify; text-indent: 40px; margin-bottom: 36px; }
  .closing { position: absolute; left: 69px; top: 1011px; font-size: 17.5px; }
  .signature { position: absolute; left: 69px; top: 1084px; font-size: 17.5px; }
</style>
</head>
<body>
<div class="letterhead">
  <div class="mascot-watermark" role="img" aria-label="Faint light grey bulldog illustration standing across the page as a watermark"></div>

  <svg class="swoosh" viewBox="0 0 850 1200" aria-hidden="true">
    <defs>
      <linearGradient id="topBand" x1="0" y1="0" x2="1" y2="0">
        <stop offset="0" stop-color="var(--blue-deep)"/>
        <stop offset="1" stop-color="var(--cyan)"/>
      </linearGradient>
      <linearGradient id="bottomBand" x1="0" y1="0" x2="1" y2="0">
        <stop offset="0" stop-color="var(--cyan)"/>
        <stop offset="1" stop-color="var(--blue-deep)"/>
      </linearGradient>
    </defs>
    <path d="M0 0 H460 C330 40 140 40 0 150 Z" fill="url(#topBand)" opacity="0.35"/>
    <path d="M0 0 H300 C190 20 80 50 0 110 Z" fill="url(#topBand)"/>
    <path d="M0 0 H130 C80 10 30 30 0 60 Z" fill="var(--blue-deep)"/>
    <path d="M850 1200 H460 C600 1150 720 1130 850 1110 Z" fill="url(#bottomBand)" opacity="0.45"/>
    <path d="M850 1200 H540 C660 1170 760 1150 850 1140 Z" fill="url(#bottomBand)"/>
  </svg>

  <div class="agent-badge">Real Estate Agent ID : #0127384950</div>

  <div class="recipient">
    <div class="name">Mr. Absent Homeholder</div>
    <div>123456 Elm Street</div>
    <div>Marlow FL 3440-5360</div>
  </div>

  <div class="salutation">Dear <strong>First Name</strong></div>

  <div class="body-copy">
    <p>I am writing you, because I am interested in purchasing your property located at <span class="field">123456 Elm Street Marlow FL 3440-5360</span> I live nearby in Brookhaven and I puschages properties throught the state of PA Currently I am working on projects in the neighbourhood, which is how I learned of your property.</p>
    <p>Please call me at <span class="field">(XXX) XXXX-Local#</span> so I can tell you how we can buy your property quickly, with no hassels and most importantly, at a fair price. I purchase the hous directly from you so there are no real estate commissions or extra fees coming out of your pocket. Furthermore, I always make cash offers so you never have to worry about delays resulting from a buyer trying to qualify for a mortgage and wasting your valuable time.</p>
    <p>I'will be glade to personally tell you more about how we can work together. All call are completely confidential and there is no obligation whatsoever. Even if you are not intersted in selling at thing time call <span class="field">(xxx) xxxx-xxxx</span>, so I can help you with determining the value of your property. You should also keep this letter for your future reference, since things in life have a tendency to change unexpectedly. Thanks you for your time and consideration and I look forward to speaking with you.</p>
  </div>

  <div class="closing">Sincerely,</div>
  <div class="signature"><span class="name">Dana Whitfield</span></div>
</div>
</body>
</html>
```